NZ First of it's kind solutions directory and marketplace for busy Mums needs a business card design

We need a business card design for our new nationwide business in NZ (long term plans to go global). We provide solutions to the everyday challenges that busy Mums face by connecting them with quality communities and suppliers of carefully selected, relevant products and services. We sell direct via our online marketplace. The final design should communicate our values of inclusivity, quality and smart solutions. Colours should incorporate our logo colour palette of #477077 and #6ba8b2. Our website is at https://www.brightnestmums.example

Target Market(s)

busy Mums, Age 28 – 50, female, income over $100K, location main centres NZ primarily but NZ wide. Is likely juggling work or career with a young family. Probably had hobbies which have fallen by the wayside.
-Wants to succeed in her chosen career without compromising on family life
-to successfully juggle her career without feeling like she is compromising her children
- Is time poor, something always has to give and it’s generally her health (she’ll stay up late, get stressed)
- probably ex corporate or professional career. Has discretional income

Industry/Entity Type

Business

Contact Information for Business Card

Lena Forbisher, Founder, BrightNestMums.example (Strapline Tap; Gather; Sorted), 47 Kowhai Terrace, Ellerslie, Auckland 1051, New Zealand. Mob: 021 483 517 Ph: +64 (0)9 571 4860

Font styles to use
Other font styles liked:
• Raleway, and/or Architects Daughter

Colors
00a990
33b8a4
86cfc6
cfeae6

Requirements
Must have
• the above details, streamline. the logo and colours associated with those logos
Should not have
• foil or metallic colours

```html
<!DOCTYPE html>
<html lang="en">
<head>
<meta charset="utf-8">
<title>BrightNest Mums – Business Card</title>
<link href="https://fonts.googleapis.com/css2?family=Fredoka:wght@600&family=Roboto:ital,wght@0,400;1,400&display=swap" rel="stylesheet">
<style>
  :root {
    --brand-deep: #477077;
    --brand-light: #6ba8b2;
    --card-front: #3f616a;
    --card-back: #f4f4f4;
    --ink: #3a3f42;
    --page: #e4e4e4;
    --white: #ffffff;
  }
  * { margin: 0; padding: 0; box-sizing: border-box; }
  html, body {
    width: 1200px; height: 576px; overflow: hidden;
    background: var(--page);
  }
  .stage { position: relative; width: 1200px; height: 576px; }

  .card {
    position: absolute;
    border-radius: 11px;
    overflow: hidden;
  }

  /* Front */
  .card-front {
    left: 82px; top: 138px; width: 485px; height: 294px;
    background: var(--card-front);
    color: var(--white);
    text-align: center;
  }
  .front-wordmark {
    position: absolute; left: 0; right: 0; top: 98px;
    font-family: "Fredoka", sans-serif;
    font-weight: 600;
    font-size: 46px;
    line-height: 1;
    letter-spacing: -0.5px;
  }
  .front-strapline {
    position: absolute; left: 0; right: 0; top: 170px;
    font-family: "Roboto", sans-serif;
    font-size: 14px;
    letter-spacing: 5.5px;
  }

  /* Back */
  .card-back {
    left: 602px; top: 138px; width: 482px; height: 292px;
    background: var(--card-back);
    font-family: "Roboto", sans-serif;
    color: var(--ink);
  }
  .holder-name {
    position: absolute; left: 22px; top: 44px;
    font-family: "Fredoka", sans-serif;
    font-weight: 600;
    font-size: 19px;
    color: var(--brand-deep);
  }
  .holder-role {
    position: absolute; left: 22px; top: 68px;
    font-style: italic; font-size: 12px;
  }
  .back-brand {
    position: absolute; right: 22px; top: 40px;
    display: flex; align-items: center; gap: 8px;
  }
  .back-brand-dot {
    width: 22px; height: 22px; border-radius: 50%;
    background: var(--brand-light);
  }
  .back-wordmark {
    font-family: "Fredoka", sans-serif;
    font-weight: 600;
    font-size: 25px;
    color: var(--brand-deep);
  }
  .address {
    position: absolute; left: 26px; top: 155px;
    font-size: 12px; line-height: 18px; font-style: normal;
  }
  .contact-list {
    position: absolute; left: 26px; top: 203px;
    list-style: none; font-size: 12px;
  }
  .contact-list li {
    display: flex; align-items: center; height: 18px;
  }
  .contact-icon {
    width: 10px; height: 10px; margin-right: 11px;
    fill: var(--brand-deep);
  }
</style>
</head>
<body>
<div class="stage">

  <section class="card card-front" aria-label="Card front">
    <div class="front-wordmark">BrightNest Mums</div>
    <div class="front-strapline">TAP | GATHER | SORTED</div>
  </section>

  <section class="card card-back" aria-label="Card back">
    <h1 class="holder-name">Lena Forbisher</h1>
    <p class="holder-role">Founder</p>

    <div class="back-brand">
      <span class="back-brand-dot"></span>
      <span class="back-wordmark">BrightNest Mums</span>
    </div>

    <address class="address">
      47 Kowhai Terrace, Ellerslie,<br>
      Auckland 1051, New Zealand
    </address>

    <ul class="contact-list">
      <li>
        <svg class="contact-icon" viewBox="0 0 10 10" aria-hidden="true"><rect x="2" y="0" width="6" height="10" rx="1.2"/><rect x="3" y="1.5" width="4" height="6" fill="#f4f4f4"/></svg>
        021 483 517
      </li>
      <li>
        <svg class="contact-icon" viewBox="0 0 10 10" aria-hidden="true"><path d="M0 3 Q5 0 10 3 L9 4.5 L7 4 L7 3 Q5 2.3 3 3 L3 4 L1 4.5Z"/><rect x="1.5" y="5" width="7" height="4.5" rx="0.8"/></svg>
        +64 (0)9 571 4860
      </li>
      <li>
        <svg class="contact-icon" viewBox="0 0 10 10" aria-hidden="true"><rect x="0" y="2" width="10" height="6.5" rx="0.5"/><path d="M0.5 2.5 L5 6 L9.5 2.5" fill="none" stroke="#f4f4f4" stroke-width="0.9"/></svg>
        www.BrightNestMums.example
      </li>
      <li>
        <svg class="contact-icon" viewBox="0 0 10 10" aria-hidden="true"><circle cx="5" cy="5" r="4.6"/><path d="M0.6 5 H9.4 M5 0.4 V9.6 M5 0.4 Q2 5 5 9.6 M5 0.4 Q8 5 5 9.6" fill="none" stroke="#f4f4f4" stroke-width="0.6"/></svg>
        lena@brightnestmums.example
      </li>
    </ul>
  </section>

</div>
</body>
</html>
```